Furniture & Lighting Wholesaler Needs a Product Catalogue/Look Book

Our company, Vostre Merchant Co, imports quality hand-made furniture, lighting and decor from South Africa. Our products are well-designed and are designed to be used in up-market hotels and homes. Our primary customers are small- to medium-size retail shops.
We require a +/- 14-16 page look book (concept as per attached image) that will be used both in hard-copy and online. We have all of the necessary high-res images, descriptions/text etc. We need you to propose several design concepts from which we can choose, and then execute the design.
Please visit our website www.vostremerchant.example to see the products and their descriptions, as well as to get a feel for our style. Thank you for looking at our project!
Target Market(s)
Boutique Furniture Stores; Interior Designers
Industry/Entity Type
It Company
Font styles to use
Other font styles liked:
- Bauer Bodini and Open Sans Condensed
Look and feel
Each slider illustrates characteristics of the customer's brand and the style your logo design should communicate.

```html
<!DOCTYPE html>
<html lang="en">
<head>
<meta charset="utf-8">
<title>Vostre Merchant Co — Furniture Look Book, pages 4–5</title>
<link href="https://fonts.googleapis.com/css2?family=Inter:wght@400;600;800&family=Open+Sans:wght@400;600;700&display=swap" rel="stylesheet">
<style>
  :root{
    --backdrop:#dcdcd8;
    --paper:#ffffff;
    --ink:#141414;
    --muted:#555555;
    --olive:#a39766;
    --olive-light:#b9ad7c;
    --olive-dark:#8c8154;
    --card-grey:#d9d9d9;
    --card-grey-dark:#bdbdbd;
    --photo-grey:#8a8a88;
  }
  *{box-sizing:border-box;margin:0;padding:0}
  html,body{width:1200px;height:804px;overflow:hidden}
  body{background:var(--backdrop);font-family:"Open Sans",Arial,sans-serif;color:var(--ink)}
  .spread{position:absolute;left:60px;top:20px;width:1080px;height:764px;display:flex;box-shadow:0 6px 24px rgba(0,0,0,.12)}
  .page{position:relative;width:540px;height:764px;background:var(--paper);overflow:hidden}
  .page--left{background:linear-gradient(90deg,#ffffff 90%,#f1f1f1 100%)}

  /* left page */
  .running-head{position:absolute;left:40px;top:30px;display:flex;align-items:center;gap:8px;font-size:7px;color:var(--muted)}
  .running-head__dot{width:10px;height:10px;border-radius:50%;background:var(--ink)}
  .running-head__sep{color:#999}
  .accent-bar{position:absolute;left:0;top:130px;width:10px;height:250px;background:var(--olive)}
  .section-tag{position:absolute;right:50px;top:62px;width:72px;height:72px;border:2px solid var(--ink);border-radius:50%;display:flex;flex-direction:column;align-items:center;justify-content:center;gap:6px;font-size:10px;font-weight:600}
  .section-tag__dash{width:22px;height:3px;background:var(--ink)}
  .headline{position:absolute;left:56px;top:110px;font-family:"Inter",Arial,sans-serif;font-weight:800;font-size:56px;line-height:1.02;letter-spacing:-1px}
  .lede{position:absolute;left:60px;top:252px;width:440px;font-size:10.5px;line-height:1.45;color:#222}
  .bullets{position:absolute;left:110px;top:318px;list-style:none;font-size:9px;line-height:1.9;color:#222}
  .bullets li::before{content:"";display:inline-block;width:5px;height:5px;border-radius:50%;background:var(--olive);margin-right:6px;vertical-align:middle}
  .photo-frame{position:absolute;left:80px;top:468px;width:272px;height:262px;border:1px solid #e2e2e2;background:#fff;padding:18px}
  .photo{width:100%;height:100%}
  .photo--trunk{background:radial-gradient(ellipse at 50% 45%,#8f806a 0%,#6b5c48 60%,#4c4134 100%)}
  .product-info{position:absolute;left:372px;top:548px;width:130px}
  .product-info__name{font-size:9px;font-weight:700}
  .product-info__desc{margin-top:6px;font-size:6px;line-height:1.5;color:var(--muted)}
  .product-info__row{display:flex;justify-content:space-between;align-items:flex-end;margin-top:42px}
  .price{font-size:10px;font-weight:600}
  .price sup{font-size:6px}
  .icons{display:flex;gap:4px}
  .icon{width:11px;height:11px;border:1px solid #333;display:block}
  .swatches{display:flex;gap:2px;margin-top:8px}
  .swatch{width:12px;height:12px}
  .folio{position:absolute;bottom:22px;font-size:8px;color:var(--muted)}
  .folio--left{left:40px}
  .folio--right{right:40px}

  /* right page */
  .hero{position:absolute;left:0;top:0;width:540px;height:470px;background:radial-gradient(ellipse at 40% 35%,var(--olive-light) 0%,var(--olive) 55%,var(--olive-dark) 100%)}
  .feature-card{position:absolute;right:48px;top:245px;width:132px;height:132px;background:rgba(255,255,255,.14);color:#fff;text-align:center;padding-top:20px}
  .feature-card__icon{display:block;margin:0 auto 10px;width:30px;height:30px}
  .feature-card__name{font-size:11px;font-weight:700}
  .feature-card__price{font-size:9px;margin-top:2px}
  .feature-card__price sup{font-size:6px}
  .feature-card__desc{font-size:5.5px;line-height:1.4;margin:6px 14px 0;opacity:.85}
  .range{position:absolute;left:55px;top:500px;display:flex;gap:16px}
  .product-card{width:135px;height:196px;background:#fff;border:1px solid #e4e4e4;display:flex;flex-direction:column}
  .product-card__photo{height:92px;margin:8px;background:linear-gradient(180deg,#f4f4f4 0%,var(--photo-grey) 50%,#f4f4f4 100%)}
  .product-card__band{background:var(--olive);color:#f3efdf;font-size:6px;padding:4px 8px}
  .product-card__body{flex:1;background:linear-gradient(180deg,var(--card-grey) 0%,var(--card-grey-dark) 100%);padding:7px 8px}
  .product-card__name{font-size:8.5px;font-weight:700}
  .product-card__desc{font-size:5.5px;line-height:1.4;color:#444;margin-top:3px}
  .product-card__row{display:flex;justify-content:space-between;align-items:flex-end;margin-top:8px}
  .product-card .price{font-size:9px}
</style>
</head>
<body>
<main class="spread">
  <section class="page page--left">
    <header class="running-head">
      <span class="running-head__dot"></span>
      <span>www.vostremerchant.example</span>
      <span class="running-head__sep">|</span>
      <span>Vostre Merchant Co. Indigenous African Design</span>
    </header>
    <div class="accent-bar"></div>
    <div class="section-tag"><span>furniture</span><span class="section-tag__dash"></span></div>
    <h1 class="headline">Your plan<br>your furniture</h1>
    <p class="lede">Elluptate dolutem sit eror amus sit dolorpore sim qui conseriti ommolla borehenet imendem voluptio ommoluptae pe coris alicature pelescid quo inihil iscita.</p>
    <ul class="bullets">
      <li>Mendum et in re, dionitus Mae niae con rehenti erendam</li>
      <li>Noctus a cus et venductum orditum te et non hica depsess</li>
      <li>Aximilis simium nu se elique pro mor inatiuute consul</li>
    </ul>
    <figure class="photo-frame">
      <div class="photo photo--trunk" role="img" aria-label="Photo of the Kestrel Trunk, a hide-covered chest with brass studs"></div>
    </figure>
    <div class="product-info">
      <h2 class="product-info__name">Kestrel Trunk</h2>
      <p class="product-info__desc">Hand-stitched hide over a solid frame, finished with brass studs and clasps. Made to order in small batches.</p>
      <div class="product-info__row">
        <span class="price"><sup>$</sup>775</span>
        <span class="icons"><span class="icon"></span><span class="icon"></span><span class="icon"></span></span>
      </div>
      <div class="swatches">
        <span class="swatch" style="background:#3d3630"></span>
        <span class="swatch" style="background:#6b5240"></span>
        <span class="swatch" style="background:#9a8260"></span>
        <span class="swatch" style="background:#c9dcea"></span>
        <span class="swatch" style="background:#9fbcd6"></span>
      </div>
    </div>
    <span class="folio folio--left">4</span>
  </section>

  <section class="page page--right">
    <div class="hero" role="img" aria-label="Photo of the Marlow Table, a round leather-laced top on three crossed dark legs, on an olive background"></div>
    <aside class="feature-card">
      <svg class="feature-card__icon" viewBox="0 0 30 30" aria-hidden="true">
        <rect x="1" y="1" width="28" height="28" fill="none" stroke="#fff" stroke-width="1.5"/>
        <rect x="8" y="12" width="14" height="8" fill="#fff"/>
        <rect x="6" y="10" width="18" height="3" fill="#fff"/>
      </svg>
      <div class="feature-card__name">Marlow Table</div>
      <div class="feature-card__price"><sup>$</sup>350</div>
      <p class="feature-card__desc">Leather top laced by hand on folding wood legs.</p>
    </aside>
    <div class="range">
      <article class="product-card">
        <div class="product-card__photo" role="img" aria-label="Photo of the Canvas Chest with Stripe"></div>
        <div class="product-card__band">Hide and hessian finish.</div>
        <div class="product-card__body">
          <h3 class="product-card__name">Canvas Chest with Stripe</h3>
          <p class="product-card__desc">Sturdy canvas body with striped hide panels.</p>
          <div class="product-card__row"><span class="price"><sup>$</sup>825</span><span class="icons"><span class="icon"></span><span class="icon"></span><span class="icon"></span></span></div>
        </div>
      </article>
      <article class="product-card">
        <div class="product-card__photo" role="img" aria-label="Photo of the Halden Chair"></div>
        <div class="product-card__band">Studded leather seat back.</div>
        <div class="product-card__body">
          <h3 class="product-card__name">Halden Chair</h3>
          <p class="product-card__desc">Curved frame with soft leather upholstery.</p>
          <div class="product-card__row"><span class="price"><sup>$</sup>1,750</span><span class="icons"><span class="icon"></span><span class="icon"></span><span class="icon"></span></span></div>
        </div>
      </article>
      <article class="product-card">
        <div class="product-card__photo" role="img" aria-label="Photo of the Tallis Side Table"></div>
        <div class="product-card__band">Carved tapered leg detail.</div>
        <div class="product-card__body">
          <h3 class="product-card__name">Tallis Side Table</h3>
          <p class="product-card__desc">Slim round top on crossed tapered legs.</p>
          <div class="product-card__row"><span class="price"><sup>$</sup>475</span><span class="icons"><span class="icon"></span><span class="icon"></span><span class="icon"></span></span></div>
        </div>
      </article>
    </div>
    <span class="folio folio--right">5</span>
  </section>
</main>
</body>
</html>
```